Website Design for Employee Moral and Happiness Company

Looking for a clean website design that explains our features in a step by step manner so our visitors know exactly what our site does before logging in.

The site is called "Velrato". See logo design and video for a sample of style and an overview of what we do.

Target Market(s)

Business owners that are looking to retain employees.

Number of Pages Required

1 page

```html
<!DOCTYPE html>
<html lang="en">
<head>
<meta charset="utf-8">
<title>Velrato — Employee Morale and Happiness</title>
<link rel="stylesheet" href="https://fonts.googleapis.com/css2?family=Frank+Ruhl+Libre:wght@500;700&family=Inter:wght@400;500;600&family=Poppins:wght@400;500&display=swap">
<style>
:root{
  --orange:#e0591d;
  --orange-deep:#c94a12;
  --ink:#1d1d1f;
  --text:#3a3a3a;
  --muted:#6b6b6b;
  --light:#eef0f3;
  --white:#ffffff;
  --black:#050505;
}
*{margin:0;padding:0;box-sizing:border-box}
html,body{width:1200px;height:4107px;overflow:hidden;background:var(--white)}
body{position:relative;font-family:"Inter",sans-serif;color:var(--text)}
.abs{position:absolute}
.serif{font-family:"Frank Ruhl Libre",serif}
.btn{position:absolute;background:var(--orange);color:var(--white);border-radius:22px;font-family:"Frank Ruhl Libre",serif;font-weight:700;font-size:15px;display:flex;align-items:center;justify-content:center}

/* header */
.site-header{position:absolute;left:0;top:0;width:1200px;height:97px;background:var(--white)}
.brand{position:absolute;left:112px;top:8px;font-family:"Frank Ruhl Libre",serif;font-weight:700;font-size:66px;color:var(--ink);letter-spacing:1px}
.nav{position:absolute;top:38px;display:flex;font-family:"Poppins",sans-serif;font-size:15px;color:#333}
.nav span{position:absolute;white-space:nowrap}
.nav .active{color:var(--orange)}
.search-icon{position:absolute;left:922px;top:38px}
.btn-contact{left:970px;top:29px;width:118px;height:38px;font-family:"Poppins",sans-serif;font-weight:500;font-size:15px}

/* hero (children positioned relative to the hero box, which starts at y=97) */
.hero{position:absolute;left:0;top:97px;width:1200px;height:660px}
.hero-title{position:absolute;left:112px;top:88px;color:var(--white);line-height:1}
.hero-title .small{font-size:72px;font-weight:500;display:block}
.hero-title .big{font-size:126px;font-weight:700;display:block;margin-top:4px}
.hero-copy{position:absolute;left:112px;top:298px;width:560px;color:#f1f1f1;font-size:18px;line-height:31px}
.btn-start{left:112px;top:382px;width:118px;height:38px}
.dots{position:absolute;display:flex;gap:6px}
.dots i{width:9px;height:9px;border-radius:50%;background:#fff;display:block}
.dots i.on{background:var(--orange)}

/* section headings */
.section-title{position:absolute;width:1200px;left:0;text-align:center;font-family:"Frank Ruhl Libre",serif;font-weight:500;font-size:33px;color:var(--ink)}

/* about */
.about-photo{position:absolute;left:192px;top:800px;width:314px;height:356px;border-radius:50%;background:radial-gradient(circle at 60% 45%,#c9c3bd,#7d8591 60%,#3f4650)}
.about-title{position:absolute;left:600px;top:828px;font-family:"Frank Ruhl Libre",serif;font-weight:500;font-size:33px;color:var(--ink)}
.about-copy{position:absolute;left:600px;top:886px;width:488px;font-size:14.5px;line-height:25.7px;text-align:justify;color:var(--text)}
.btn-learn{left:600px;top:1093px;width:118px;height:38px}

/* features */
.features{position:absolute;left:0;top:1240px;width:1200px;height:702px;background:linear-gradient(180deg,#f2f3f5,#e9ebee)}
.timeline-line{position:absolute;left:174px;width:3px;background:var(--orange-deep)}
.node{position:absolute;width:80px;height:80px;border-radius:50%;border:3px solid var(--orange);background:var(--white);display:flex;align-items:center;justify-content:center}
.node span{width:60px;height:60px;border-radius:50%;background:var(--orange);display:flex;align-items:center;justify-content:center}
.branch{position:absolute;height:2px;background:var(--orange)}
.branch::after{content:"";position:absolute;right:-4px;top:-4px;width:10px;height:10px;border-radius:50%;background:var(--orange)}
.end-dot{position:absolute;width:10px;height:10px;border-radius:50%;background:var(--orange-deep)}
.feature-head{position:absolute;left:222px;font-weight:600;font-size:15.5px;color:var(--ink)}
.feature-copy{position:absolute;left:222px;top:1469px;width:350px;font-size:14.5px;line-height:25.7px;text-align:justify}
.feature-photo-back{position:absolute;left:652px;top:1437px;width:445px;height:403px;border-radius:20px;background:var(--orange)}
.feature-photo{position:absolute;left:645px;top:1430px;width:443px;height:400px;border-radius:20px;background:linear-gradient(120deg,#cfc7bd,#a99b89 45%,#3a3d44 80%)}

/* video */
.video-frame{position:absolute;left:167px;top:2097px;width:868px;height:380px;border-radius:40px;background:linear-gradient(110deg,#1f3b5d 0%,#2f6a6b 40%,#9b9690 60%,#a7a39c 100%);box-shadow:0 12px 24px rgba(0,0,0,.18)}
.play{position:absolute;left:560px;top:2248px;width:80px;height:80px;border-radius:50%;background:var(--orange);box-shadow:0 0 0 12px rgba(224,89,29,.3);display:flex;align-items:center;justify-content:center}

/* blog */
.blog{position:absolute;left:0;top:2563px;width:1200px;height:524px;background:linear-gradient(180deg,#e4621f,#d9561b)}
.blog-sub{position:absolute;left:0;width:1200px;top:2685px;text-align:center;color:#ffd9c4;font-size:14.5px;line-height:25px}
.blog-card{position:absolute;top:2770px;width:306px;height:251px;color:var(--white)}
.blog-card .t{position:absolute;left:24px;font-weight:500;font-size:17.5px;line-height:22px;width:260px}
.blog-card .d{position:absolute;left:24px;font-size:14px;font-weight:500}
.arrow{position:absolute;top:2876px}

/* testimonials */
.t-card{position:absolute;top:3225px;width:473px;height:310px;background:var(--white);box-shadow:0 4px 18px rgba(0,0,0,.12)}
.avatar{position:absolute;left:28px;top:28px;width:116px;height:116px;border-radius:50%;border:4px solid var(--orange);background:radial-gradient(circle at 50% 40%,#a9a29b,#3a4151 70%)}
.t-name{position:absolute;left:173px;top:26px;font-family:"Poppins",sans-serif;font-weight:500;font-size:22px;color:var(--ink)}
.t-role{position:absolute;left:173px;top:60px;font-size:14px;color:var(--muted)}
.t-copy{position:absolute;left:173px;top:103px;width:288px;font-style:italic;font-size:14.5px;line-height:27px;color:var(--muted);text-align:justify}
.quote{position:absolute;left:48px;top:145px;font-family:"Frank Ruhl Libre",serif;font-size:150px;color:#b8b8b8;line-height:1}

/* footer */
.footer{position:absolute;left:0;top:3770px;width:1200px;height:337px;background:var(--black);color:#e8e8e8}
.footer-brand{position:absolute;left:112px;top:3808px;font-family:"Frank Ruhl Libre",serif;font-weight:700;font-size:62px;color:var(--white)}
.social{position:absolute;top:3928px;display:flex;gap:6px;left:112px}
.social i{width:36px;height:36px;border-radius:50%;display:block;background:var(--white)}
.social i:first-child{background:var(--orange)}
.vdiv{position:absolute;left:390px;top:3790px;width:1px;height:180px;background:#333}
.col-title{position:absolute;top:3786px;color:var(--orange);font-family:"Poppins",sans-serif;font-weight:500;font-size:19px}
.col-list{position:absolute;top:3830px;font-size:14.5px;line-height:25.7px;color:#e6e6e6}
.contact-row{position:absolute;left:864px;display:flex;gap:10px;font-size:14.5px;line-height:25px;color:#e6e6e6}
.hdiv{position:absolute;left:112px;top:3998px;width:976px;height:1px;background:#2b2b2b}
.copyright{position:absolute;left:0;width:1200px;top:4038px;text-align:center;font-size:14.5px;color:#e6e6e6}
</style>
</head>
<body>

<header class="site-header">
  <div class="brand">Velrato</div>
  <nav class="nav">
    <span class="active" style="left:424px">HOME</span>
    <span style="left:511px">ABOUT</span>
    <span style="left:605px">OUR FEATURES</span>
    <span style="left:757px">VIDEO</span>
    <span style="left:846px">BLOG</span>
  </nav>
  <svg class="search-icon" width="18" height="18" viewBox="0 0 18 18"><circle cx="7.5" cy="7.5" r="5.5" fill="none" stroke="#e0591d" stroke-width="2.5"/><path d="M11.5 11.5 16 16" stroke="#e0591d" stroke-width="2.8" stroke-linecap="round"/></svg>
  <div class="btn btn-contact">CONTACT</div>
</header>

<section class="hero">
  <svg class="abs" style="left:0;top:0" width="1200" height="660" viewBox="0 0 1200 660">
    <defs>
      <linearGradient id="heroTone" x1="0" y1="0" x2="1" y2="1">
        <stop offset="0" stop-color="#4b5560"/>
        <stop offset=".45" stop-color="#8d969f"/>
        <stop offset=".75" stop-color="#5a6a7c"/>
        <stop offset="1" stop-color="#2e3a48"/>
      </linearGradient>
    </defs>
    <path d="M0 0H1200V585Q600 693 0 585Z" fill="#e0591d"/>
    <path d="M0 0H1200V520Q600 626 0 520Z" fill="url(#heroTone)" role="img" aria-label="Photo of smiling colleagues walking through a bright office corridor"/>
  </svg>
  <h1 class="hero-title serif"><span class="small">Welcome to</span><span class="big">Velrato</span></h1>
  <p class="hero-copy">Lorem ipsum dolor sit amet, consectetur adipiscing elit, sed do eiusmod tempor incididunt ut labore et dolore magna aliqua.</p>
  <div class="btn btn-start">Get Started</div>
  <div class="dots" style="left:578px;top:586px"><i></i><i class="on"></i><i></i><i></i></div>
</section>

<section class="about">
  <div class="about-photo" role="img" aria-label="Photo of a smiling businessman holding a phone in a meeting room"></div>
  <h2 class="about-title">About Velrato</h2>
  <p class="about-copy">Lorem ipsum dolor sit amet, consectetur adipiscing elit, sed do eiusmod tempor incididunt ut labore et dolore magna aliqua. Ut enim ad minim veniam, quis nostrud exercitation ullamco laboris nisi ut aliquip ex ea commodo consequat. Duis aute irure dolor in reprehenderit in voluptate velit esse cillum dolore eu fugiat nulla pariatur. Excepteur sint occaecat cupidatat non proident, sunt in culpa qui officia deserunt mollit anim id est laborum.</p>
  <div class="btn btn-learn">Learn More</div>
</section>

<section class="features"></section>
<h2 class="section-title" style="top:1300px">Our Features</h2>
<div class="timeline-line" style="top:1292px;height:598px"></div>
<div class="end-dot" style="left:170px;top:1287px"></div>
<div class="end-dot" style="left:170px;top:1883px"></div>

<div class="branch" style="left:214px;top:1416px;width:206px"></div>
<div class="node" style="left:135px;top:1377px"><span>
  <svg width="30" height="30" viewBox="0 0 30 30" fill="none" stroke="#fff" stroke-width="2"><rect x="4" y="6" width="22" height="20" rx="2"/><path d="M4 12h22M10 3v6M20 3v6M9 17h3M15 17h3M21 17h2M9 22h3M15 22h3"/></svg>
</span></div>
<div class="feature-head" style="top:1435px">Sed ut perspiciatis unde omnis iste</div>
<p class="feature-copy">Lorem ipsum dolor sit amet, consectetur adipiscing elit, sed do eiusmod tempor incididunt ut labore et dolore magna aliqua. Ut enim ad minim veniam, quis nostrud exercitation ullamco laboris nisi ut aliquip ex ea commodo consequat.</p>

<div class="branch" style="left:214px;top:1664px;width:206px"></div>
<div class="node" style="left:135px;top:1625px"><span>
  <svg width="30" height="30" viewBox="0 0 30 30" fill="none" stroke="#fff" stroke-width="2"><rect x="4" y="9" width="22" height="16" rx="2"/><path d="M11 9V6h8v3M4 15h22M14 15v3h2v-3"/></svg>
</span></div>
<div class="feature-head" style="top:1684px">Sed ut perspiciatis unde omnis</div>

<div class="branch" style="left:214px;top:1806px;width:206px"></div>
<div class="node" style="left:135px;top:1767px"><span>
  <svg width="30" height="30" viewBox="0 0 30 30" fill="none" stroke="#fff" stroke-width="2"><circle cx="15" cy="13" r="5"/><path d="M15 4v3M15 19v3M6 13h3M21 13h3M8.5 6.5l2 2M19.5 17.5l2 2M21.5 6.5l-2 2M10.5 17.5l-2 2M5 27h20"/></svg>
</span></div>
<div class="feature-head" style="top:1826px">Sed ut perspiciatis unde omnis</div>

<div class="feature-photo-back"></div>
<div class="feature-photo" role="img" aria-label="Photo of a smiling woman with glasses at a laptop talking with a colleague"></div>

<section class="video">
  <h2 class="section-title" style="top:2021px">Our Videos</h2>
  <div class="video-frame" role="img" aria-label="Illustration of a man working at a laptop surrounded by mail, chat and calendar icons"></div>
  <div class="play"><svg width="26" height="28" viewBox="0 0 26 28"><path d="M4 2 24 14 4 26Z" fill="#fff"/></svg></div>
</section>

<section class="blog" role="img" aria-label="Orange tinted photo of a keyboard"></section>
<h2 class="section-title" style="top:2630px;color:#fff">Latest Blog</h2>
<p class="blog-sub">Lorem ipsum dolor sit amet, consectetur adipiscing elit, sed do eiusmod<br>tempor incididunt ut labore et dolore magna aliqua.</p>
<svg class="arrow" style="left:74px" width="24" height="40" viewBox="0 0 24 40"><path d="M20 2 4 20l16 18" fill="none" stroke="#fff" stroke-width="2.5"/></svg>
<svg class="arrow" style="left:1104px" width="24" height="40" viewBox="0 0 24 40"><path d="M4 2l16 18L4 38" fill="none" stroke="#fff" stroke-width="2.5"/></svg>

<article class="blog-card" style="left:112px;background:linear-gradient(180deg,#8e8f93,#3e4552)" role="img" aria-label="Photo of colleagues shaking hands">
  <div class="t" style="top:164px">Lorem ipsum dolor sit amet, consectetur adipiscing elit</div>
  <div class="d" style="top:218px">09 Mar 2022</div>
</article>
<article class="blog-card" style="left:447px;background:linear-gradient(180deg,#6b5d52,#26272c)" role="img" aria-label="Photo of a smiling man at a desk">
  <div class="t" style="top:82px">Lorem ipsum dolor sit amet, consectetur adipiscing elit</div>
  <div class="d" style="top:136px">09 Mar 2022</div>
  <div class="d" style="top:210px;display:flex;align-items:center;gap:8px">Read More
    <svg width="18" height="18" viewBox="0 0 18 18"><circle cx="9" cy="9" r="7.5" fill="none" stroke="#fff" stroke-width="1.2"/><path d="M8 6l3 3-3 3" fill="none" stroke="#fff" stroke-width="1.2"/></svg></div>
</article>
<article class="blog-card" style="left:782px;background:linear-gradient(180deg,#a39d97,#3d4350)" role="img" aria-label="Photo of a team celebrating in the office">
  <div class="t" style="top:164px">Lorem ipsum dolor sit amet, consectetur adipiscing elit</div>
  <div class="d" style="top:218px">09 Mar 2022</div>
</article>

<section class="testimonials">
  <h2 class="section-title" style="top:3156px">Testimonials</h2>
  <article class="t-card" style="left:112px">
    <div class="avatar" role="img" aria-label="Portrait photo of the reviewer"></div>
    <div class="quote">“</div>
    <div class="t-name">Marisol Teague</div>
    <div class="t-role">Lorem ipsum dolor</div>
    <p class="t-copy">Lorem ipsum dolor sit amet, consectetur adipiscing elit, sed do eiusmod tempor incididunt ut labore et dolore magna aliqua. Ut enim ad minim veniam, quis nostrud exercitation ullamco laboris nisi ut aliquip ex ea commodo consequat. ”</p>
  </article>
  <article class="t-card" style="left:615px">
    <div class="avatar" role="img" aria-label="Portrait photo of the reviewer"></div>
    <div class="quote">“</div>
    <div class="t-name">Dorian Fairley</div>
    <div class="t-role">Lorem ipsum dolor</div>
    <p class="t-copy">Lorem ipsum dolor sit amet, consectetur adipiscing elit, sed do eiusmod tempor incididunt ut labore et dolore magna aliqua. Ut enim ad minim veniam, quis nostrud exercitation ullamco laboris nisi ut aliquip ex ea commodo consequat. ”</p>
  </article>
  <div class="dots" style="left:578px;top:3579px"><i style="background:#bdbdbd"></i><i class="on"></i><i style="background:#bdbdbd"></i></div>
</section>

<svg class="abs" style="left:0;top:3630px" width="1200" height="150" viewBox="0 0 1200 150">
  <path d="M0 130Q600 -60 1200 130V150H0Z" fill="#e0591d"/>
  <path d="M0 150Q600 -20 1200 150Z" fill="#050505"/>
</svg>
<footer class="footer"></footer>
<div class="footer-brand">Velrato</div>
<div class="social"><i></i><i></i><i></i><i></i></div>
<div class="vdiv"></div>

<div class="col-title" style="left:432px">Quick Links</div>
<div class="col-list" style="left:432px">Home<br>About<br>Our features<br>Video<br>Blog</div>

<div class="col-title" style="left:639px">Our Company</div>
<div class="col-list" style="left:639px">Terms&amp;condtions<br>Privacy Policy<br>About Us<br>Support</div>

<div class="col-title" style="left:864px">Contact us</div>
<div class="contact-row" style="top:3830px">
  <svg width="13" height="18" viewBox="0 0 13 18" style="margin-top:5px"><path d="M6.5 0A6.5 6.5 0 0 0 0 6.5C0 11 6.5 18 6.5 18S13 11 13 6.5A6.5 6.5 0 0 0 6.5 0Zm0 9a2.5 2.5 0 1 1 0-5 2.5 2.5 0 0 1 0 5Z" fill="#fff"/></svg>
  <span>Lorem ipsum dolor sit amet,<br>consectetur</span>
</div>
<div class="contact-row" style="top:3896px">
  <svg width="16" height="16" viewBox="0 0 16 16" style="margin-top:5px"><path d="M3.5 1 6 4 4.5 6a9 9 0 0 0 5.5 5.5L12 10l3 2.5-1.5 2.5C7 15 1 9 1 2.5Z" fill="#fff"/></svg>
  <span>+1(555) 010 0199</span>
</div>
<div class="contact-row" style="top:3938px">
  <svg width="16" height="12" viewBox="0 0 16 12" style="margin-top:8px"><rect width="16" height="12" rx="1" fill="#fff"/><path d="M1 1l7 6 7-6" fill="none" stroke="#050505" stroke-width="1.3"/></svg>
  <span>info@velrato.com</span>
</div>

<div class="hdiv"></div>
<div class="copyright">©Copyrights 2022 Velrato &nbsp; | &nbsp; All Rights Reserved</div>

</body>
</html>
```